Global (re)insurance broker needs a business card design

We need a classic business card for our company that is headquartered in SG, with offices in Malaysia and Dubai. We specialise in insurance and reinsurance broking and consultancy for our global clients.

```html
<!DOCTYPE html>
<html lang="en">
<head>
<meta charset="utf-8">
<title>Halvern – Business Card</title>
<link rel="stylesheet" href="https://fonts.googleapis.com/css2?family=Open+Sans:wght@400;700&display=swap">
<style>
  :root {
    --canvas: #2b2b2f;
    --card: #151515;
    --brand-blue: #2a4a9e;
    --brand-mint: #c4dfbb;
    --ink-light: #f2f2f2;
  }
  * { margin: 0; padding: 0; box-sizing: border-box; }
  html, body {
    width: 1200px; height: 947px; overflow: hidden;
    background: var(--canvas);
    font-family: "Open Sans", Arial, sans-serif;
  }
  .canvas {
    position: relative; width: 1200px; height: 947px;
    display: flex; flex-direction: column; align-items: center; justify-content: center; gap: 40px;
  }
  .card {
    position: relative; width: 620px; height: 354px;
    background: var(--card); border-radius: 22px; overflow: hidden;
    box-shadow: 0 18px 40px rgba(0,0,0,.45);
  }
  .card-front { display: flex; align-items: center; justify-content: center; }
  .wordmark {
    font-weight: 700; color: var(--brand-mint); letter-spacing: 4px; line-height: 1;
  }
  .card-front .wordmark { font-size: 86px; }
  .card-back .wordmark {
    position: absolute; left: 46px; top: 150px; font-size: 46px; letter-spacing: 2px;
  }
  .divider {
    position: absolute; left: 330px; top: 46px; width: 1px; height: 236px;
    background: var(--brand-mint);
  }
  .contact {
    position: absolute; left: 352px; top: 44px; color: var(--ink-light);
  }
  .person-name { font-size: 23px; font-weight: 700; line-height: 1.1; }
  .person-name .first { color: var(--brand-blue); }
  .person-name .last { color: var(--ink-light); }
  .person-role { font-size: 15px; margin-top: 2px; }
  .contact-list { list-style: none; margin-top: 16px; font-size: 14px; line-height: 1.45; }
  .contact-list li { display: flex; align-items: center; gap: 8px; }
  .contact-list svg { width: 12px; height: 12px; flex: none; }
  .address { font-style: normal; font-size: 14px; line-height: 1.45; margin-top: 14px; }
  .swoosh { position: absolute; left: 0; top: 0; width: 620px; height: 354px; }
</style>
</head>
<body>
<main class="canvas">
  <section class="card card-front" aria-label="Card front">
    <span class="wordmark">HALVERN</span>
  </section>

  <section class="card card-back" aria-label="Card back">
    <svg class="swoosh" viewBox="0 0 620 354" aria-hidden="true">
      <path d="M0 354 C 180 300 380 262 620 228 L 620 240 C 400 272 200 312 70 354 Z" fill="var(--brand-blue)"/>
      <path d="M90 354 C 250 312 420 282 620 256 L 620 354 Z" fill="var(--brand-mint)"/>
    </svg>
    <span class="wordmark">HALVERN</span>
    <div class="divider"></div>
    <div class="contact">
      <p class="person-name"><span class="first">Mei Lin</span> <span class="last">Ong</span></p>
      <p class="person-role">Chief Operating Officer</p>
      <ul class="contact-list">
        <li><svg viewBox="0 0 12 12"><path d="M2.5 1 L4.5 1 L5.3 3.5 L4 4.5 C4.6 6 6 7.4 7.5 8 L8.5 6.7 L11 7.5 L11 9.5 C11 10.3 10.3 11 9.5 11 C5 11 1 7 1 2.5 C1 1.7 1.7 1 2.5 1 Z" fill="var(--ink-light)"/></svg>+65 9123 4567</li>
        <li><svg viewBox="0 0 12 12"><rect x="1" y="2.5" width="10" height="7" rx="1" fill="var(--ink-light)"/><path d="M1.5 3 L6 6.5 L10.5 3" stroke="var(--card)" stroke-width="1" fill="none"/></svg>meilin@halvern.com</li>
        <li><svg viewBox="0 0 12 12"><circle cx="6" cy="6" r="5" fill="var(--ink-light)"/><path d="M1 6 H11 M6 1 C3.5 3.5 3.5 8.5 6 11 M6 1 C8.5 3.5 8.5 8.5 6 11" stroke="var(--card)" stroke-width=".8" fill="none"/></svg>www.halvern.com</li>
      </ul>
      <address class="address">28 Cecil Street,<br>Harbour Tower #12-04,<br>Singapore 069543</address>
    </div>
  </section>
</main>
</body>
</html>
```